Brindovalle Business cards

Dear team, I need to get the design file to suit it to our team. The focus of the business card is the Automotive Market and the design must be in black colour and the logo must be in glossy black. On the front of the card I need to get the following info:

- Name and Surname
- Title
- eMail
- Phone Number
- Skype account
- domain address

```html
<!DOCTYPE html>
<html lang="en">
<head>
<meta charset="utf-8">
<title>Brindovalle Business Cards</title>
<link rel="stylesheet" href="https://fonts.googleapis.com/css2?family=Open+Sans:wght@400;600;700&display=swap">
<style>
  :root {
    --stage: #161616;
    --card: #262626;
    --card-edge: #1e1e1e;
    --gloss: #0d0d0d;
    --red: #ee2e36;
    --ink: #f2f2f2;
  }
  * { margin: 0; padding: 0; box-sizing: border-box; }
  html, body { width: 1200px; height: 900px; overflow: hidden; }
  body {
    background: var(--stage);
    font-family: "Open Sans", Arial, sans-serif;
    position: relative;
  }
  .card {
    position: absolute;
    left: 250px;
    width: 700px;
    height: 400px;
    background: linear-gradient(135deg, var(--card) 0%, var(--card-edge) 100%);
    box-shadow: 0 14px 30px rgba(0,0,0,.6);
    overflow: hidden;
  }
  .card::after {
    content: "";
    position: absolute;
    left: 0; right: 0; bottom: 0;
    height: 9px;
    background: var(--red);
  }
  .card--back { top: 30px; }
  .card--front { top: 470px; }

  .brand-gloss {
    position: absolute;
    left: 120px; top: 150px;
    display: flex; align-items: center; gap: 16px;
    color: var(--gloss);
    font-weight: 700;
    font-size: 52px;
    letter-spacing: -0.5px;
  }
  .brand-gloss .dot {
    width: 56px; height: 56px; border-radius: 50%;
    background: var(--gloss);
  }

  .brand-mark {
    position: absolute;
    left: 40px; top: 170px;
    display: flex; align-items: center; gap: 12px;
    color: var(--red);
    font-weight: 700;
    font-size: 34px;
  }
  .brand-mark .dot {
    width: 40px; height: 40px; border-radius: 50%;
    background: var(--red);
  }
  .divider {
    position: absolute;
    left: 330px; top: 95px;
    width: 3px; height: 210px;
    background: var(--red);
  }
  .details {
    position: absolute;
    left: 365px; top: 92px;
    color: var(--ink);
  }
  .person-name {
    color: var(--red);
    font-weight: 700;
    font-size: 30px;
    letter-spacing: .5px;
    line-height: 1.05;
  }
  .person-title { font-size: 19px; margin-bottom: 16px; }
  .address { font-size: 19px; line-height: 1.3; margin-bottom: 14px; }
  .contact { list-style: none; font-size: 19px; line-height: 1.32; }
  .contact li { display: flex; align-items: center; gap: 8px; }
  .contact svg { width: 15px; height: 15px; flex: none; }
</style>
</head>
<body>
  <section class="card card--back" aria-label="Card back">
    <div class="brand-gloss"><span class="dot"></span>Brindovalle.com</div>
  </section>

  <section class="card card--front" aria-label="Card front">
    <div class="brand-mark"><span class="dot"></span>Brindovalle</div>
    <div class="divider"></div>
    <div class="details">
      <h1 class="person-name">DARIO KESTEL</h1>
      <p class="person-title">Director</p>
      <p class="address">2841 W Halden,<br>Norbury, Kansas 66218</p>
      <ul class="contact">
        <li>
          <svg viewBox="0 0 16 16" aria-hidden="true"><path fill="#ee2e36" d="M4 1l2.5 3-1.4 1.6c.8 2 2.3 3.5 4.3 4.3L11 8.5l3 2.5-1.5 3C7 14 2 9 2 3.5z"/></svg>
          555-014-2276
        </li>
        <li>
          <svg viewBox="0 0 16 16" aria-hidden="true"><rect x="1" y="3" width="14" height="10" fill="#ee2e36"/><path d="M1 3l7 6 7-6" fill="none" stroke="#262626" stroke-width="1.4"/></svg>
          info@brindovalle.com
        </li>
        <li>
          <svg viewBox="0 0 16 16" aria-hidden="true"><circle cx="8" cy="8" r="6.5" fill="none" stroke="#ee2e36" stroke-width="1.6"/></svg>
          brindovalle
        </li>
      </ul>
    </div>
  </section>
</body>
</html>
```